Update our OBGYN business card look and info

We are an OBGYN office. Our logo is nice but would like to "woman" part of the logo to be a darker color, to contrast with the flower that surrounds it. Maybe make our practice name Bloom Harbor Health more feminine. Our practice caters to women only. All providers and staff are female.

Target Market(s)

Females 16-65.

Industry/Entity Type

Business

Contact Information for Business Card

See attached upload. The ONLY CHANGE to the information is DELETE the name Paula Renwick, Midwife and REPLACE with Dora Fintelli, Midwife

Logo Text

Bloom Harbor Health Obstetrics & Gynecology

Font styles to use
Serif
Script

Colors
85cae6
0692cd
33a6d7
85abd2
f59195
eea4c8
cadf82
fac994
d3a5cc

```html
<!DOCTYPE html>
<html lang="en">
<head>
<meta charset="utf-8">
<title>Bloom Harbor Health – Business Card</title>
<link href="https://fonts.googleapis.com/css2?family=Cookie&family=Jost:wght@400;500&display=swap" rel="stylesheet">
<style>
  :root {
    --backdrop: #3b3c3e;
    --teal: #7cc2d3;
    --teal-text: #6fbccf;
    --white: #ffffff;
    --grey: #747474;
    --grey-dark: #5f5f5f;
  }
  * { box-sizing: border-box; margin: 0; padding: 0; }
  html, body { width: 1200px; height: 859px; overflow: hidden; }
  body {
    background: var(--backdrop);
    font-family: "Jost", "Futura", sans-serif;
    position: relative;
  }
  .card {
    position: absolute;
    width: 520px;
    height: 297px;
    border-radius: 16px;
    overflow: hidden;
  }
  .brand-dot { width: 46px; height: 46px; border-radius: 50%; background: var(--white); flex: none; }
  .brand-name { font-family: "Cookie", cursive; font-weight: 400; font-size: 42px; line-height: 0.95; }
  .brand-sub { font-size: 14px; font-weight: 500; letter-spacing: 0.6px; margin-top: 2px; }

  /* Front */
  .card-front { left: 140px; top: 120px; background: var(--teal); }
  .front-brand {
    position: absolute; left: 60px; top: 186px;
    display: flex; align-items: center; gap: 14px;
    color: var(--white);
  }

  /* Back */
  .card-back { left: 540px; top: 430px; background: var(--white); }
  .back-wave { position: absolute; inset: 0; }
  .back-brand {
    position: absolute; right: 34px; top: 18px;
    display: flex; align-items: center; gap: 14px;
    color: var(--teal-text);
  }
  .back-brand .brand-dot { background: var(--teal-text); width: 52px; height: 52px; }
  .back-brand .brand-sub { color: var(--grey-dark); }
  .providers {
    position: absolute; right: 28px; top: 140px;
    list-style: none; text-align: right;
    color: var(--white); font-size: 14px; line-height: 20px; letter-spacing: 0.5px;
  }
  .contact {
    position: absolute; left: 30px; bottom: 20px;
    color: var(--white); font-size: 15px; letter-spacing: 0.8px; line-height: 21px;
  }
  .contact-address { margin-bottom: 6px; }
  .contact-line { display: flex; align-items: center; gap: 9px; }
  .contact-line svg { width: 14px; height: 14px; flex: none; }
</style>
</head>
<body>

<section class="card card-front" aria-label="Card front">
  <div class="front-brand">
    <span class="brand-dot"></span>
    <div>
      <div class="brand-name">Bloom Harbor Health</div>
      <div class="brand-sub">Obstetrics &amp; Gynecology</div>
    </div>
  </div>
</section>

<section class="card card-back" aria-label="Card back">
  <svg class="back-wave" viewBox="0 0 520 297" preserveAspectRatio="none" aria-hidden="true">
    <path d="M0 122 C 100 144, 250 132, 380 116 C 460 106, 505 84, 520 54 L520 297 L0 297 Z" fill="#7cc2d3"/>
    <path d="M0 116 C 100 138, 250 126, 380 110 C 460 100, 505 78, 520 48" fill="none" stroke="#747474" stroke-width="6"/>
  </svg>

  <div class="back-brand">
    <span class="brand-dot"></span>
    <div>
      <div class="brand-name">Bloom Harbor Health</div>
      <div class="brand-sub">Obstetrics &amp; Gynecology</div>
    </div>
  </div>

  <ul class="providers">
    <li>Marian Ostrowe, MD</li>
    <li>Lena Calloway, MD</li>
    <li>Ruth Delacorte, MD</li>
    <li>Dora Fintelli, Midwife</li>
    <li>Nora Wexley, Midwife</li>
  </ul>

  <div class="contact">
    <div class="contact-address">418 Harbor Lane, Ste 3B<br>Riverton, GA 30999 - 0142</div>
    <div class="contact-line">
      <svg viewBox="0 0 24 24" aria-hidden="true"><path fill="#fff" d="M6.6 10.8a15.1 15.1 0 0 0 6.6 6.6l2.2-2.2c.3-.3.7-.4 1-.2 1.1.4 2.3.6 3.6.6.6 0 1 .4 1 1V20c0 .6-.4 1-1 1A17 17 0 0 1 3 4c0-.6.4-1 1-1h3.5c.6 0 1 .4 1 1 0 1.3.2 2.5.6 3.6.1.3 0 .7-.2 1z"/></svg>
      <span>(555) 214-0387</span>
    </div>
    <div class="contact-line">
      <svg viewBox="0 0 24 24" aria-hidden="true"><path fill="#fff" d="M4 21V8h6V3h10v18zm2-2h2v-2H6zm0-4h2v-2H6zm6 4h2v-2h-2zm0-4h2v-2h-2zm0-4h2V9h-2zm4 8h2v-2h-2zm0-4h2v-2h-2zm0-4h2V9h-2zm0-4h2V5h-2z"/></svg>
      <span>(555) 214-0391</span>
    </div>
    <div class="contact-line">
      <svg viewBox="0 0 24 24" aria-hidden="true"><circle cx="12" cy="12" r="9" fill="none" stroke="#fff" stroke-width="2"/><path d="M3 12h18M12 3c3 3 3 15 0 18M12 3c-3 3-3 15 0 18" fill="none" stroke="#fff" stroke-width="1.6"/></svg>
      <span>bloomharborhealth.example</span>
    </div>
  </div>
</section>

</body>
</html>
```